MRT Property - Business Cards

Looking for a business card & general letterhead, signage etc design for our new logo.

Colours:
000a20
0056a2
00b5ef
0088ce
68cef2

Fonts:
Poppins
Karla

Please keep look and feel of new brand - example in the zip package I sent.

```html
<!DOCTYPE html>
<html lang="en">
<head>
<meta charset="UTF-8">
<title>MRT Property – Business Cards</title>
<link href="https://fonts.googleapis.com/css2?family=Poppins:wght@400;500;600&family=Karla:wght@400;500&display=swap" rel="stylesheet">
<style>
  :root {
    --ink: #000a20;
    --card: #151b2c;
    --card-deep: #0f1423;
    --royal: #0056a2;
    --sky: #00b5ef;
    --ocean: #0088ce;
    --ice: #68cef2;
    --gloss: #2a3042;
    --muted: #9aa3b5;
    --text: #e6e9f0;
    --backdrop: #1b1b1d;
  }
  * { margin: 0; padding: 0; box-sizing: border-box; }
  html, body {
    width: 1200px;
    height: 852px;
    overflow: hidden;
    background: var(--backdrop);
  }
  .sheet {
    position: relative;
    width: 1200px;
    height: 852px;
    display: flex;
    align-items: center;
    justify-content: center;
    gap: 60px;
  }
  .card {
    position: relative;
    width: 520px;
    height: 297px;
    border-radius: 18px;
    overflow: hidden;
    background: linear-gradient(150deg, var(--card) 0%, var(--card-deep) 100%);
    box-shadow: 0 18px 40px rgba(0, 0, 0, 0.55);
  }

  /* Front */
  .card-front .brand {
    position: absolute;
    left: 60px;
    top: 104px;
    display: flex;
    align-items: center;
    gap: 14px;
  }
  .card-front .brand-name {
    font-family: "Poppins", sans-serif;
    font-weight: 600;
    font-size: 44px;
    color: var(--gloss);
    letter-spacing: 0.5px;
  }
  .card-front .brand-dot {
    width: 22px;
    height: 22px;
    border-radius: 50%;
    background: var(--gloss);
  }
  .card-front .web {
    position: absolute;
    right: 34px;
    bottom: 34px;
    font-family: "Poppins", sans-serif;
    font-size: 11px;
    letter-spacing: 4px;
    color: var(--muted);
  }
  .card-front .band {
    position: absolute;
    left: 0;
    right: 0;
    bottom: 0;
    height: 12px;
    background: var(--royal);
  }

  /* Back */
  .card-back .brand {
    position: absolute;
    left: 34px;
    top: 86px;
    display: flex;
    align-items: center;
    gap: 10px;
  }
  .card-back .brand-name {
    font-family: "Poppins", sans-serif;
    font-weight: 600;
    font-size: 30px;
    color: var(--royal);
  }
  .card-back .brand-dot {
    width: 14px;
    height: 14px;
    border-radius: 50%;
    background: var(--ocean);
  }
  .person {
    position: absolute;
    left: 34px;
    top: 150px;
  }
  .person-name {
    font-family: "Poppins", sans-serif;
    font-weight: 600;
    font-size: 17px;
    color: var(--ocean);
    line-height: 1.2;
  }
  .person-role {
    font-family: "Poppins", sans-serif;
    font-size: 10.5px;
    color: var(--text);
  }
  .contacts {
    position: absolute;
    left: 34px;
    top: 196px;
    list-style: none;
  }
  .contacts li {
    display: flex;
    align-items: center;
    gap: 10px;
    height: 20px;
    font-family: "Karla", sans-serif;
    font-size: 12.5px;
    color: var(--text);
  }
  .contacts svg {
    width: 12px;
    height: 12px;
    fill: var(--ice);
    flex: none;
  }
</style>
</head>
<body>
<main class="sheet">

  <section class="card card-front" aria-label="Business card front">
    <div class="brand">
      <span class="brand-name">MRT Property</span>
      <span class="brand-dot"></span>
    </div>
    <p class="web">www.mrtproperty.com</p>
    <div class="band"></div>
  </section>

  <section class="card card-back" aria-label="Business card back">
    <div class="brand">
      <span class="brand-name">MRT Property</span>
      <span class="brand-dot"></span>
    </div>
    <div class="person">
      <p class="person-name">Daniel Hale</p>
      <p class="person-role">Managing Director</p>
    </div>
    <ul class="contacts">
      <li>
        <svg viewBox="0 0 24 24" aria-hidden="true"><path d="M6.6 10.8a15.1 15.1 0 0 0 6.6 6.6l2.2-2.2a1 1 0 0 1 1-.25 11.4 11.4 0 0 0 3.6.57 1 1 0 0 1 1 1V20a1 1 0 0 1-1 1A17 17 0 0 1 3 4a1 1 0 0 1 1-1h3.5a1 1 0 0 1 1 1c0 1.25.2 2.45.57 3.6a1 1 0 0 1-.25 1z"/></svg>
        555-010-2040
      </li>
      <li>
        <svg viewBox="0 0 24 24" aria-hidden="true"><path d="M2 5h20v14H2zm2 2v.5l8 5 8-5V7zm0 2.8V17h16V9.8l-8 5z"/></svg>
        daniel@mrtproperty.com
      </li>
      <li>
        <svg viewBox="0 0 24 24" aria-hidden="true"><path d="M12 2a10 10 0 1 0 0 20 10 10 0 0 0 0-20zm6.9 6h-2.9a15.7 15.7 0 0 0-1.4-3.6A8 8 0 0 1 18.9 8zM12 4c.8 1.2 1.5 2.5 1.9 4h-3.8c.4-1.5 1.1-2.8 1.9-4zM4.3 14a8 8 0 0 1 0-4h3.4a16 16 0 0 0 0 4zm.8 2h2.9c.3 1.3.8 2.5 1.4 3.6A8 8 0 0 1 5.1 16zM8 8H5.1a8 8 0 0 1 4.3-3.6C8.8 5.5 8.3 6.7 8 8zm4 12c-.8-1.2-1.5-2.5-1.9-4h3.8c-.4 1.5-1.1 2.8-1.9 4zm2.3-6H9.7a14.6 14.6 0 0 1 0-4h4.6a14.6 14.6 0 0 1 0 4zm.3 5.6c.6-1.1 1.1-2.3 1.4-3.6h2.9a8 8 0 0 1-4.3 3.6zm1.7-5.6a16 16 0 0 0 0-4h3.4a8 8 0 0 1 0 4z"/></svg>
        www.mrtproperty.com
      </li>
      <li>
        <svg viewBox="0 0 24 24" aria-hidden="true"><path d="M12 2a7 7 0 0 0-7 7c0 5.2 7 13 7 13s7-7.8 7-13a7 7 0 0 0-7-7zm0 9.5A2.5 2.5 0 1 1 12 6.5a2.5 2.5 0 0 1 0 5z"/></svg>
        27 Harbour View Road Ryde
      </li>
    </ul>
  </section>

</main>
</body>
</html>
```